Maple Roster Business Card for recruitment company

We are looking for a Business Card Design that incorporates our personal details and our busines name and logo. We are a specialized search consultancy that recruit Property and Construction professionals.
We would like a business card that stands out and is appealing to the Construction and Property industry as well.

Target Market(s)

people in the construction and property industry

Contact Information for Business Card

Business Name and logo

Font styles to use
Serif

Colors
0094D4
00A9DD
6FCCEA
C7EBF8
E9F6FB

Requirements
Must have
• Business name and logo as well as contact details
Should not have
• No photos of us please

```html
<!DOCTYPE html>
<html lang="en">
<head>
<meta charset="utf-8">
<title>Maple Roster – Business Card</title>
<link rel="stylesheet" href="https://fonts.googleapis.com/css2?family=Questrial&family=Poppins:wght@600&display=swap">
<style>
  :root {
    --backdrop: #2b2c2d;
    --card-white: #ffffff;
    --card-fade: #ececec;
    --navy: #0b3a52;
    --navy-deep: #06283a;
    --band-slate: #314447;
    --text-grey: #3a3f42;
    --reverse-text: #f2f4f5;
  }
  * { margin: 0; padding: 0; box-sizing: border-box; }
  html, body {
    width: 1200px;
    height: 732px;
    overflow: hidden;
    background: var(--backdrop);
  }
  .stage {
    position: relative;
    width: 1200px;
    height: 732px;
  }
  .card {
    position: absolute;
    top: 242px;
    width: 436px;
    height: 248px;
    box-shadow: 0 8px 18px rgba(0, 0, 0, 0.45);
    overflow: hidden;
  }
  .card-front {
    left: 144px;
    background: linear-gradient(160deg, var(--card-white) 0%, var(--card-fade) 100%);
    font-family: "Questrial", "Century Gothic", sans-serif;
    color: var(--text-grey);
  }
  .wordmark {
    position: absolute;
    left: 21px;
    top: 20px;
    font-family: "Questrial", "Century Gothic", sans-serif;
    font-size: 25px;
    letter-spacing: 0.5px;
    color: var(--navy);
    line-height: 1;
  }
  .person {
    position: absolute;
    left: 21px;
    top: 115px;
  }
  .person-name {
    font-family: "Poppins", "Century Gothic", sans-serif;
    font-weight: 600;
    font-size: 16px;
    color: var(--navy);
    line-height: 20px;
  }
  .person-role {
    font-size: 13px;
    line-height: 15px;
    color: var(--text-grey);
  }
  .contact-list {
    position: absolute;
    left: 21px;
    top: 163px;
    list-style: none;
    font-size: 13px;
    line-height: 14.5px;
  }
  .contact-list .label {
    display: inline-block;
    width: 19px;
    font-family: "Poppins", "Century Gothic", sans-serif;
    font-weight: 600;
    font-size: 11px;
    color: var(--navy);
  }
  .location {
    position: absolute;
    left: 21px;
    top: 216px;
    font-size: 13px;
  }
  .band {
    position: absolute;
    left: 0;
    bottom: 0;
    width: 436px;
    height: 7px;
    display: block;
  }
  .card-back {
    left: 621px;
    background: radial-gradient(ellipse at 40% 30%, #0d4660 0%, var(--navy) 45%, var(--navy-deep) 100%);
  }
  .card-back .texture {
    position: absolute;
    inset: 0;
    background: linear-gradient(120deg, rgba(255,255,255,0.04), rgba(0,0,0,0.12));
  }
  .back-name {
    position: absolute;
    left: 0;
    right: 0;
    top: 112px;
    text-align: center;
    font-family: "Questrial", "Century Gothic", sans-serif;
    font-size: 24px;
    letter-spacing: 0.5px;
    color: var(--reverse-text);
    line-height: 1;
  }
</style>
</head>
<body>
<main class="stage">
  <section class="card card-front" aria-label="Business card front">
    <div class="wordmark">MAPLE ROSTER</div>
    <div class="person">
      <p class="person-name">Clara Whitfield</p>
      <p class="person-role">Director &nbsp;|&nbsp; Senior Search Consultant</p>
    </div>
    <ul class="contact-list">
      <li><span class="label">T:</span> +64 21 555 0142</li>
      <li><span class="label">E:</span> clara@mapleroster.nz</li>
      <li><span class="label">W:</span> www.mapleroster.nz</li>
    </ul>
    <p class="location">Hamilton, New Zealand</p>
    <svg class="band" viewBox="0 0 436 7" preserveAspectRatio="none" aria-hidden="true">
      <polygon points="0,0 242,0 236,7 0,7" fill="var(--navy)"/>
      <polygon points="242,0 248,0 242,7 236,7" fill="var(--card-white)"/>
      <polygon points="248,0 436,0 436,7 242,7" fill="var(--band-slate)"/>
    </svg>
  </section>

  <section class="card card-back" aria-label="Business card back">
    <div class="texture" role="img" aria-label="Soft navy background texture"></div>
    <p class="back-name">Maple Roster</p>
  </section>
</main>
</body>
</html>
```